Thornvale Group needs a business card design

We need a new business card design using the logo recently selected in a logo competition on Pixel Bazaar. Our business is a consultancy specializing in aviation and energy and the winning business card design will promote an image of precision and professionalism with creativity.

Please use the logo with the name on the front of the card and use a complementary font. Make the back white with either the light grey or dark grey logo.

Target Market(s)

Senior finance and legal leaders at aviation and energy companies

Industry/Entity Type

Management Consulting

Contact Information for Business Card

Peter Castrell
President
Thornvale Group

www.thornvalegroup.example

(555) 204-6391
pc@thornvalegroup.example

Requirements
Must have
• Professional font that goes well with the logo font

```html
<!DOCTYPE html>
<html lang="en">
<head>
<meta charset="utf-8">
<title>Thornvale Group — Business Card</title>
<link rel="stylesheet" href="https://fonts.googleapis.com/css2?family=Open+Sans:wght@400;600;700&display=swap">
<style>
  :root {
    --backdrop: #e4e5e7;
    --card: #ffffff;
    --navy: #1c3f6e;
    --grey-text: #5b5d60;
    --rule: #c9cbce;
    --sheen: #f1f2f5;
  }
  * { box-sizing: border-box; margin: 0; padding: 0; }
  html, body {
    width: 1200px; height: 900px; overflow: hidden;
    background: var(--backdrop);
    font-family: "Open Sans", Arial, sans-serif;
  }
  .stage {
    position: relative; width: 1200px; height: 900px;
    display: flex; flex-direction: column; align-items: center; justify-content: center;
    gap: 44px;
  }
  .card {
    position: relative; width: 580px; height: 331px;
    background: var(--card);
    box-shadow: 0 2px 10px rgba(0,0,0,0.08);
    overflow: hidden;
  }
  .wordmark {
    display: flex; align-items: center; gap: 12px;
    color: var(--navy); font-weight: 600; letter-spacing: 0.06em;
    text-transform: uppercase; white-space: nowrap;
  }
  .wordmark__dot { width: 14px; height: 14px; background: var(--navy); flex: none; }

  /* Front */
  .card--front .sheen {
    position: absolute; right: 0; bottom: 0; width: 100%; height: 100%;
    background: var(--sheen);
    clip-path: polygon(100% 38%, 100% 100%, 46% 100%);
  }
  .card--front .front-content {
    position: absolute; left: 150px; top: 92px;
  }
  .card--front .wordmark { font-size: 27px; }
  .tagline {
    margin-top: 34px; color: var(--navy); font-weight: 700; font-size: 15px;
    letter-spacing: -0.01em;
  }
  .sectors { margin-top: 2px; color: var(--grey-text); font-size: 15px; }

  /* Back */
  .card--back .wordmark {
    position: absolute; right: 48px; top: 96px; font-size: 23px;
  }
  .person { position: absolute; left: 40px; top: 118px; }
  .person__name { color: var(--navy); font-weight: 700; font-size: 19px; }
  .person__title { color: var(--grey-text); font-size: 14px; line-height: 1.1; }
  .divider {
    position: absolute; left: 210px; right: 48px; top: 168px;
    height: 1px; background: var(--rule);
  }
  .contact {
    position: absolute; right: 40px; bottom: 70px;
    list-style: none; text-align: right; color: var(--grey-text); font-size: 16px;
  }
  .contact li { display: flex; justify-content: flex-end; align-items: center; gap: 12px; line-height: 1.5; }
  .contact svg { width: 14px; height: 14px; fill: var(--navy); flex: none; }
</style>
</head>
<body>
<main class="stage">
  <section class="card card--front" aria-label="Card front">
    <div class="sheen"></div>
    <div class="front-content">
      <div class="wordmark"><span class="wordmark__dot"></span>Thornvale Group</div>
      <p class="tagline">Finance and Strategy Consulting</p>
      <p class="sectors">Aviation - Manufacturing - Energy</p>
    </div>
  </section>

  <section class="card card--back" aria-label="Card back">
    <div class="person">
      <p class="person__name">Peter J. Castrell</p>
      <p class="person__title">President</p>
    </div>
    <div class="wordmark"><span class="wordmark__dot"></span>Thornvale Group</div>
    <div class="divider"></div>
    <ul class="contact">
      <li>(555) 204-6391
        <svg viewBox="0 0 24 24" aria-hidden="true"><path d="M6.6 10.8a15.1 15.1 0 0 0 6.6 6.6l2.2-2.2c.3-.3.7-.4 1-.2 1.1.4 2.3.6 3.6.6.6 0 1 .4 1 1V20c0 .6-.4 1-1 1C10.6 21 3 13.4 3 4c0-.6.4-1 1-1h3.5c.6 0 1 .4 1 1 0 1.3.2 2.5.6 3.6.1.3 0 .7-.2 1z"/></svg>
      </li>
      <li>pc@thornvalegroup.example
        <svg viewBox="0 0 24 24" aria-hidden="true"><path d="M2 5h20v14H2z M3.5 6.5 12 13l8.5-6.5" fill="var(--navy)"/><path d="M3 6l9 7 9-7" fill="none" stroke="#fff" stroke-width="1.6"/></svg>
      </li>
    </ul>
  </section>
</main>
</body>
</html>
```